TV Antenna Installation business needs a unique flyer

We need a simple but effective flyer design for our TV Aerial installation company based in Newcastle, NSW, Australia called Bright Harbour TV & Aerial Svcs.
We are trying to target areas where there has been a new transmitter installed and most houses just require their aerial redirecting and tv's retuning.

Industry/Entity Type

Business

Requirements
Must have
• We would like the idea of a headline phrase such as " Poor TV reception……..now a thing from the past" or something similar & catchy.
Also "Did you know a new transmitter has been recently installed in your area, we can therefore now GUARANTEE 100% PERFECT PICTURE
Charges from only $95.
- Free 5 year warranty
- Free signal testing
- Free Onsite Quote
Phone 0463 527 209
Nice to have
• Other services include:

- New Installs
- Extra Points & repairs
- TV wall mounting/Home Cinema
- Pull down tall masts

Modern tv picture, see example uploaded

```html
<!DOCTYPE html>
<html lang="en">
<head>
<meta charset="utf-8">
<title>Bright Harbour TV &amp; Aerial Svcs – Flyer</title>
<link rel="stylesheet" href="https://fonts.googleapis.com/css2?family=Roboto+Condensed:ital,wght@0,400;0,700;1,700&family=PT+Sans:wght@400&display=swap">
<style>
  :root {
    --red: #e3232b;
    --red-dark: #c01a22;
    --blue: #1a5fae;
    --navy: #0a3c8c;
    --sky: #3fa9e6;
    --orange: #ee5a24;
    --orange-light: #f47a3a;
    --ink: #3a3a3a;
    --paper: #ffffff;
    --tv-yellow: #e9c93a;
  }
  * { box-sizing: border-box; margin: 0; padding: 0; }
  html, body { width: 948px; height: 1200px; overflow: hidden; background: #eeeeee; }
  .flyer {
    position: relative; width: 948px; height: 1200px; overflow: hidden;
    background: var(--paper);
    font-family: "Roboto Condensed", "Arial Narrow", sans-serif;
  }
  .corner { position: absolute; left: 0; top: 0; }
  .brand {
    position: absolute; left: 0; right: 60px; top: 42px; text-align: right;
    color: var(--red); font-weight: 700; font-size: 52px; letter-spacing: -0.3px;
  }
  .location {
    position: absolute; right: 72px; top: 112px;
    color: var(--blue); font-weight: 700; font-size: 34px;
  }
  .headline-bubble { position: absolute; left: 40px; top: 130px; }
  .headline {
    position: absolute; left: 78px; top: 180px; width: 220px;
    color: #fff; font-weight: 700; font-size: 35px; line-height: 1.05;
    text-align: center; transform: rotate(-12deg);
  }
  .tv-illustration {
    position: absolute; left: 300px; top: 200px; width: 225px; height: 255px;
    border-radius: 40px;
    background: linear-gradient(160deg, #f6dd5c, var(--tv-yellow) 60%, #c9a825);
  }
  .services { position: absolute; left: 575px; top: 215px; }
  .services h2 { color: var(--blue); font-weight: 700; font-size: 38px; margin-bottom: 14px; }
  .services ul { list-style: none; }
  .services li {
    display: flex; align-items: flex-start; gap: 12px;
    color: var(--ink); font-weight: 700; font-size: 26px; line-height: 1.3; margin-bottom: 9px;
  }
  .services li svg { flex: none; margin-top: 6px; }
  .promise {
    position: absolute; left: 39px; top: 497px; width: 866px; height: 91px;
    background: linear-gradient(180deg, var(--orange-light), var(--orange));
    color: #fff; text-align: center;
  }
  .promise .lead { font-weight: 700; font-size: 17px; padding-top: 14px; }
  .promise .claim { font-weight: 700; font-size: 32px; margin-top: 8px; }
  .room-photo {
    position: absolute; left: 39px; top: 588px; width: 866px; height: 324px;
    background: linear-gradient(100deg, #b58a4c 0%, #e9cf95 35%, #f1e3bd 60%, #d9b676 100%);
  }
  .price-tab { position: absolute; left: 50px; top: 868px; }
  .price {
    position: absolute; left: 80px; top: 878px;
    color: #fff; font-weight: 700; font-size: 34px;
  }
  .perks { position: absolute; left: 60px; top: 958px; list-style: none; }
  .perks li {
    display: flex; align-items: center; gap: 16px;
    color: var(--blue); font-weight: 700; font-size: 35px; margin-bottom: 8px;
  }
  .perks li::before {
    content: ""; width: 20px; height: 20px; border-radius: 50%; background: var(--orange);
  }
  .note {
    position: absolute; left: 522px; top: 974px; width: 384px;
    font-family: "PT Sans", Arial, sans-serif; font-size: 15px; line-height: 1.3; color: #222;
  }
  .waves { position: absolute; left: 0; bottom: 0; }
  .call {
    position: absolute; left: 0; right: 0; bottom: 20px; text-align: center; padding-left: 210px;
    color: #fff; font-weight: 700; font-size: 46px;
  }
  .call .number { font-size: 56px; }
</style>
</head>
<body>
<main class="flyer">
  <svg class="corner" width="140" height="130" viewBox="0 0 140 130" aria-hidden="true">
    <path d="M0 0 H110 Q40 20 0 120 Z" fill="var(--blue)"/>
    <path d="M0 128 Q30 30 132 6" stroke="var(--orange)" stroke-width="5" fill="none"/>
    <path d="M0 112 Q34 22 118 2" stroke="#ffffff" stroke-width="3" fill="none"/>
  </svg>

  <h1 class="brand">Bright Harbour TV &amp; Aerial SVCS</h1>
  <p class="location">Newcastle, NSW, Australia</p>

  <div class="tv-illustration" role="img" aria-label="Illustration of a yellow retro television with antennas and a signal line on screen"></div>

  <svg class="headline-bubble" width="280" height="290" viewBox="0 0 280 290" aria-hidden="true">
    <defs>
      <radialGradient id="bubbleFill" cx="45%" cy="40%" r="60%">
        <stop offset="0" stop-color="#f2444a"/>
        <stop offset="1" stop-color="var(--red-dark)"/>
      </radialGradient>
    </defs>
    <path d="M140 10 A125 125 0 1 1 120 258 L100 286 L96 252 A125 125 0 0 1 140 10 Z" fill="url(#bubbleFill)" stroke="#fff" stroke-width="4"/>
  </svg>
  <p class="headline">Poor TV Reception? Now a thing from the Past</p>

  <section class="services">
    <h2>Other services:</h2>
    <ul>
      <li><svg width="20" height="20" viewBox="0 0 20 20" aria-hidden="true"><rect x="1" y="3" width="16" height="16" fill="#fff" stroke="var(--red)" stroke-width="2"/><path d="M4 10 L9 15 L19 1" stroke="var(--red)" stroke-width="3" fill="none"/></svg>New Installs</li>
      <li><svg width="20" height="20" viewBox="0 0 20 20" aria-hidden="true"><rect x="1" y="3" width="16" height="16" fill="#fff" stroke="var(--red)" stroke-width="2"/><path d="M4 10 L9 15 L19 1" stroke="var(--red)" stroke-width="3" fill="none"/></svg>Extra Points &amp; repairs</li>
      <li><svg width="20" height="20" viewBox="0 0 20 20" aria-hidden="true"><rect x="1" y="3" width="16" height="16" fill="#fff" stroke="var(--red)" stroke-width="2"/><path d="M4 10 L9 15 L19 1" stroke="var(--red)" stroke-width="3" fill="none"/></svg><span>TV wall mounting/<br>Home Cinema</span></li>
      <li><svg width="20" height="20" viewBox="0 0 20 20" aria-hidden="true"><rect x="1" y="3" width="16" height="16" fill="#fff" stroke="var(--red)" stroke-width="2"/><path d="M4 10 L9 15 L19 1" stroke="var(--red)" stroke-width="3" fill="none"/></svg>Pull down tall masts</li>
    </ul>
  </section>

  <section class="promise">
    <p class="lead">Did you know a new transmitter has been recently installed in your area, we can therefore</p>
    <p class="claim">now GUARANTEE 100% PERFECT PICTURE</p>
  </section>

  <div class="room-photo" role="img" aria-label="Photo of a modern living room with a wall-mounted flat screen TV, speakers and lit shelf niches"></div>

  <svg class="price-tab" width="450" height="68" viewBox="0 0 450 68" aria-hidden="true">
    <path d="M4 10 Q4 2 14 2 H420 L440 62 H4 Z" fill="#7a2a12"/>
    <path d="M0 6 Q0 0 10 0 H418 L436 56 H0 Z" fill="var(--orange)"/>
  </svg>
  <p class="price">Charges from only $95</p>

  <ul class="perks">
    <li>Free 5 Year Warranty</li>
    <li>Free Signal Testing</li>
    <li>Free Onsite Quote</li>
  </ul>

  <p class="note">We are trying to target areas where there has been a new transmitter installed and most houses just require their aerial redirecting and tv's retuning.</p>

  <svg class="waves" width="948" height="180" viewBox="0 0 948 180" aria-hidden="true">
    <path d="M0 70 Q300 120 560 70 T948 30 V180 H0 Z" fill="#cde9f8"/>
    <path d="M0 84 Q300 130 580 80 T948 44" stroke="var(--sky)" stroke-width="6" fill="none"/>
    <path d="M0 100 Q320 140 600 96 T948 60 V180 H0 Z" fill="var(--sky)"/>
    <path d="M0 118 Q330 150 620 112 T948 78 V180 H0 Z" fill="var(--navy)"/>
  </svg>
  <p class="call">Call: <span class="number">0463 527 209</span></p>
</main>
</body>
</html>
```